July 2022 Industrial Manufacturer Product Expo Mexico City

We manufacture large screws and fastners for large Mining equipment, Trains, large ships, airplanes, wind turbines, and so on. We also do custom work base on the customer needs. No matter the size we can make it.
We have a Expo coming up with companies all over the world. We have to stand out we are a family own business so our customer service will be above and beyond anyone can provide. We do not have a sales force to push our products and services we provide one on one service.
Plus@!! I'm looking for anything that you designers can come up with if it was your company to put on a business card, plus i want to do a 1 or 2 sided pamphlet, and then a website. We make Speciality Bolts for large mining equipment these bolts can be 3 to 4 foot long!!! Plus fasteners, Nuts, washers, any, size, strengths, special materials, we offer more of a ono on one customer service, We are a small company, family own, but can fulfill any type of orders. We can also provide special time lines for emergency orders. "We keep the machines running we here at KRV don't believe in down time" We want to hear any slogan based on our company to stand out.
Thanks i really appreciate all your work and options that we have to pick on. Plus just a thought we could possibly want to entertain a experience Marketing internet help maybe a employment possibility. Thanks

I need 2 cards one in Spanish and English Like the steel back ground maybe send me in some bright red and blue writing Same with the Black cards Please remove the word Military The logo KRV maybe integrate a picture of a Bolt 🔩 Thank you

Still looking for I need 2 cards one in Spanish and English Like the steel back ground maybe send me in some bright red and blue writing Same with the Black cards try bright writing Please remove the word Military The logo KRV maybe integrate a picture of a Bolt 🔩 Plus will need the company to make a brochure and website next Thank you

Target Market(s)

Large Mining, Ship, Train, Green Energy, VELM, and Government equipment. Throughout the World

Industry/Entity Type

We can Custom Manufacture any type of Fastners for Mining equipment, Trains, Ships, Green energy, Governments, or military projects. wind turbines,

Contact Information for Business Card

I attached the name and contact info that's on a card, plus the Company Logo. Would like industrial looking background with Bright Colors that will stand out!! If we can insert somewhere maybe on back that we "Custom Manufacture Any Size or Quantity Fastners for Large Mining Equipment, Trains, Ships, Green Energy Equipment or Government Projects

Font styles to use
Other font styles liked:
• You Pick, has to be bold, colorful standout, Professional looking Beable to read it.

Colors

Designer to choose colors to be used in the design.

Requirements
Must have
• Need in Spanish and English TO STANDOUT FROM THE REST OF THE EXPO!! See Business card details, Rounded corners
Nice to have
• Can i see some of the darker cards with Bright Red and Blue letters I like to see the different type of card material, heavy thickness, plastic, transparent, Metal types, Bright Colors, I saw like Raised letters like on the logo.

```html
<!DOCTYPE html>
<html lang="es">
<head>
<meta charset="utf-8">
<title>KRV – Tarjetas de presentación</title>
<link rel="stylesheet" href="https://fonts.googleapis.com/css2?family=Tinos:wght@400;700&display=swap">
<style>
  :root{
    --backdrop:#c9c9c9;
    --card-white:#ffffff;
    --navy:#0a2478;
    --royal:#0b47a8;
    --sky:#0a97d9;
    --accent-blue:#1f8ae0;
    --ink-navy:#10267a;
    --band-light:#9a9a9a;
    --band-dark:#0d0d0d;
    --text-white:#ffffff;
    --text-soft:#dcecff;
    --logo-ink:#0b3c9c;
  }
  *{box-sizing:border-box;margin:0;padding:0}
  html,body{width:1200px;height:800px;overflow:hidden}
  body{
    background:var(--backdrop);
    font-family:"Tinos","Times New Roman",serif;
    display:flex;flex-direction:column;align-items:center;justify-content:center;gap:40px;
  }
  .card{
    position:relative;width:600px;height:343px;border-radius:26px;overflow:hidden;
    box-shadow:0 6px 18px rgba(0,0,0,.18);
  }
  /* Front */
  .card-front{background:var(--card-white)}
  .corner-square{
    position:absolute;top:0;right:72px;width:78px;height:62px;
    background:linear-gradient(135deg,var(--navy),var(--sky));
  }
  .contact{position:absolute;left:40px;top:70px}
  .contact-name{font-size:23px;color:var(--accent-blue);font-weight:400;margin-bottom:10px}
  .contact-role,.contact-email{font-size:17px;color:var(--ink-navy);line-height:1.25}
  .phone-band{
    position:absolute;left:0;top:222px;width:345px;height:72px;
    background:linear-gradient(160deg,var(--band-light) 0%,#4a4a4a 45%,var(--band-dark) 100%);
    display:flex;flex-direction:column;justify-content:center;padding-left:40px;
  }
  .phone-line{font-size:18px;color:var(--text-white);letter-spacing:.5px;line-height:1.25}
  .phone-line b{font-weight:700}
  .brand-front{
    position:absolute;left:360px;top:120px;
    font-size:88px;font-weight:700;color:var(--logo-ink);letter-spacing:4px;line-height:1;
  }
  /* Back */
  .card-back{
    background:linear-gradient(170deg,var(--navy) 0%,var(--royal) 40%,var(--sky) 100%);
    display:flex;flex-direction:column;align-items:center;justify-content:center;text-align:center;
    padding:0 30px;
  }
  .brand-back{
    font-size:88px;font-weight:700;color:var(--text-white);letter-spacing:8px;line-height:1;
    margin-bottom:22px;
  }
  .tagline{font-size:16px;color:var(--text-white);line-height:1.3}
  .tagline-es{margin-top:12px;color:var(--text-soft)}
</style>
</head>
<body>
  <article class="card card-front" aria-label="Frente de la tarjeta">
    <div class="corner-square"></div>
    <div class="contact">
      <p class="contact-name">Lic. Mariana Solís Vega</p>
      <p class="contact-role">Cotizaciones en</p>
      <p class="contact-email">ventas.krvpernos@correo.mx</p>
    </div>
    <div class="phone-band">
      <p class="phone-line"><b>P:</b> 8714402518</p>
      <p class="phone-line"><b>M:</b> 8716630291</p>
    </div>
    <p class="brand-front">KRV</p>
  </article>

  <article class="card card-back" aria-label="Reverso de la tarjeta">
    <p class="brand-back">KRV</p>
    <p class="tagline tagline-en" lang="en">Custom Manufacture Any Size or Quantity Fastners for Large<br>Mining Equipment, Trains, Ships, Green Energy Equipment<br>or Government Projects</p>
    <p class="tagline tagline-es">Fabricación a la medida de tornillería de cualquier tamaño o cantidad<br>para equipo minero, trenes, barcos, equipo de energía verde<br>o proyectos de gobierno</p>
  </article>
</body>
</html>
```